Business Report Cover

We need a revamped quarterly report cover to send to our clients. We asset manage commercial and residential properties throughout the the United States. We use a .pdf version of a cover that we've used for years but would like a fresh updated look for 2018. The cover should include our company logo (KOV Enterprises) and a photo of the property as well as the Quarter/Year of the report.

```html
<!DOCTYPE html>
<html lang="en">
<head>
<meta charset="utf-8">
<title>Quarterly Operating Report – 1st Quarter 2018</title>
<link href="https://fonts.googleapis.com/css2?family=Didact+Gothic&family=Poppins:wght@500&display=swap" rel="stylesheet">
<style>
  :root {
    --brand-green: #0e773b;
    --paper: #ffffff;
    --ink: #111111;
    --backdrop: #ecebe8;
    --photo-sky: #c9ccd2;
    --photo-ground: #4b4a4f;
  }
  html, body {
    margin: 0;
    width: 1200px;
    height: 1200px;
    overflow: hidden;
    background: var(--backdrop);
  }
  .report-cover {
    position: absolute;
    left: 204px;
    top: 40px;
    width: 792px;
    height: 1120px;
    background: var(--paper);
    box-shadow: 0 2px 8px rgba(0,0,0,0.12);
  }
  .report-cover svg { display: block; width: 100%; height: 100%; }
  .band { fill: var(--brand-green); }
  .cover-title {
    font-family: "Didact Gothic", sans-serif;
    font-size: 38px;
    fill: var(--ink);
    letter-spacing: -0.5px;
  }
  .cover-year {
    font-family: "Poppins", sans-serif;
    font-weight: 500;
    font-size: 122px;
    fill: var(--ink);
    letter-spacing: -4px;
  }
  .property-address {
    font-family: "Didact Gothic", sans-serif;
    font-size: 22px;
    fill: var(--ink);
  }
  .company-name {
    font-family: "Didact Gothic", sans-serif;
    fill: var(--ink);
  }
  .company-name .name-main { font-size: 60px; letter-spacing: 1px; }
  .company-name .name-sub { font-size: 15px; letter-spacing: 5px; }
</style>
</head>
<body>
  <div class="report-cover">
    <svg viewBox="0 0 990 1400" xmlns="http://www.w3.org/2000/svg">
      <defs>
        <linearGradient id="propertyPhotoTone" x1="0" y1="0" x2="0" y2="1">
          <stop offset="0" stop-color="var(--photo-sky)"/>
          <stop offset="0.5" stop-color="#8a8580"/>
          <stop offset="1" stop-color="var(--photo-ground)"/>
        </linearGradient>
      </defs>

      <!-- top framing -->
      <rect class="band" x="0" y="0" width="990" height="63"/>
      <polygon class="band" points="0,63 138,63 0,398"/>

      <text class="cover-title" x="933" y="237" text-anchor="end">QUARTERLY OPERATING REPORT</text>
      <text class="cover-title" x="933" y="285" text-anchor="end">1ST QUARTER</text>

      <g role="img" aria-label="Photo of the property: a convenience store with fuel canopy and pumps">
        <polygon points="222,350 990,350 990,928 0,928" fill="url(#propertyPhotoTone)"/>
      </g>

      <!-- lower framing -->
      <rect class="band" x="0" y="928" width="990" height="64"/>
      <polygon class="band" points="853,992 990,992 990,1330"/>

      <text class="cover-year" x="96" y="1120">2018</text>

      <text class="property-address" x="86" y="1289">Harborline Market</text>
      <text class="property-address" x="88" y="1321">4120 NE Cedar Point Dr.</text>
      <text class="property-address" x="86" y="1352">Ridgefield, WA 98642</text>

      <text class="company-name" text-anchor="middle">
        <tspan class="name-main" x="805" y="1324">KOV</tspan>
        <tspan class="name-sub" x="808" y="1355">ENTERPRISES</tspan>
      </text>
    </svg>
  </div>
</body>
</html>
```